Payday Lending App Interface Design

Hello, we are building a payday lending application, Lendoro, that lend people money. I have drafted some of the screens that show the functionalities we have at the moment, please find the screens in attachments.
The elements in the screens are placed just to show what should be included in those screens, it's not necessary to follow the same layout. If you have better design ideas, you are very welcomed to show off your talent.
I think what we want is a style guide so that we can apply the same style to any screens that are similar to the ones I attached. We really like
the style as in the attached image called Style.png. We might want something similar - a simple, clean design yet fun and engaging. Customised graphical elements such as icons, illustrations are preferable.
Apart from the attached screens, we might also need a design for the On Board screen and the Login/Sign Up screen too.
Our logo colour is in yellow and black. Perhaps we will have a similar colour theme. I also attached the logo file, icon-Lendoro.png, if you would like to put it in your design.
Please message me if you need further information.
Regards
Target Market(s)
Young people that doesn't have strong income

```html
<!DOCTYPE html>
<html lang="en">
<head>
<meta charset="utf-8">
<title>Lendoro – App Screens</title>
<link href="https://fonts.googleapis.com/css2?family=Quicksand:wght@500;600;700&family=Roboto:wght@400;500&display=swap" rel="stylesheet">
<style>
  :root {
    --page: #f2f2f2;
    --bar: #2b2b2b;
    --ink: #161616;
    --white: #ffffff;
    --gold-1: #fcc20e;
    --gold-2: #f9b000;
    --gold-3: #f7a400;
    --muted: #666666;
    --dots: #ececec;
  }
  * { box-sizing: border-box; margin: 0; padding: 0; }
  html, body { width: 1200px; height: 782px; overflow: hidden; background: var(--page); }
  .stage {
    position: absolute; left: 0; top: 0;
    width: 1439px; height: 938px;
    transform: scale(0.8339); transform-origin: 0 0;
  }
  .phone {
    position: absolute; top: 59px; width: 420px; height: 817px;
    background: linear-gradient(160deg, var(--gold-1) 0%, var(--gold-2) 50%, var(--gold-3) 100%);
    font-family: 'Quicksand', sans-serif; color: var(--ink);
    overflow: hidden;
  }
  .phone--personal { left: 63px; }
  .phone--loan { left: 512px; }
  .phone--bank { left: 963px; }
  .status-bar {
    position: absolute; top: 0; left: 0; right: 0; height: 60px; background: var(--bar);
  }
  .status-bar .back { position: absolute; left: 8px; top: 19px; }
  .status-bar .indicators { position: absolute; right: 6px; top: 20px; }
  .nav-bar {
    position: absolute; bottom: 0; left: 0; right: 0; height: 52px; background: var(--bar);
    display: flex; justify-content: space-between; align-items: center; padding: 0 36px 0 36px;
  }
  .brand {
    position: absolute; left: 0; right: 0;
    display: flex; justify-content: center; align-items: center; gap: 14px;
  }
  .brand .mark { width: 58px; height: 58px; border-radius: 14px; background: var(--ink); }
  .brand .name { font-size: 44px; font-weight: 700; color: var(--ink); }
  .screen-title {
    position: absolute; left: 0; right: 0; text-align: center;
    font-size: 36px; font-weight: 700; line-height: 1;
  }
  .field {
    position: absolute; left: 28px; width: 365px; height: 50px; background: var(--white);
    border-radius: 3px; font-family: 'Roboto', sans-serif; font-size: 16px; color: #333;
    padding-left: 17px; line-height: 50px;
  }
  .btn-next {
    position: absolute; left: 28px; top: 583px; width: 365px; height: 54px; background: var(--ink);
    border-radius: 4px; color: var(--white); font-family: 'Roboto', sans-serif; font-size: 22px;
    text-align: center; line-height: 52px; border-bottom: 3px solid #000;
  }
  .centered { position: absolute; left: 0; right: 0; text-align: center; }
  .next-label { top: 263px; font-size: 19px; font-weight: 500; }
  .amount { top: 292px; font-size: 84px; font-weight: 700; line-height: 1; }
  .due { top: 379px; font-size: 22px; font-weight: 500; }
  .toggle {
    position: absolute; left: 38px; top: 421px; width: 345px; height: 65px;
    border: 2px solid var(--ink); display: flex;
  }
  .toggle span { flex: 1; display: flex; align-items: center; justify-content: center; font-size: 24px; font-weight: 700; }
  .toggle .active { background: var(--ink); color: var(--white); }
  .activities {
    position: absolute; left: 12px; top: 523px; width: 394px; height: 220px; border: 1px solid var(--ink);
  }
  .activities h2 {
    height: 59px; border-bottom: 1px solid var(--ink); text-align: center;
    font-size: 30px; font-weight: 700; line-height: 59px;
  }
  .activity { position: relative; height: 75px; padding: 16px 20px 0 19px; }
  .activity .label { font-size: 22px; font-weight: 500; line-height: 1.1; }
  .activity .date { font-size: 15px; font-weight: 500; margin-top: 6px; }
  .activity .value { position: absolute; right: 21px; top: 17px; font-size: 20px; font-weight: 500; }
  .bank-card {
    position: absolute; left: 22px; width: 378px; height: 87px; background: var(--white);
    border-radius: 3px;
  }
  .bank-card .tile {
    position: absolute; left: 10px; top: 9px; width: 76px; height: 69px;
    border: 1px solid #e2e2e2; border-radius: 4px; display: flex; align-items: center; justify-content: center;
  }
  .tile .dot { width: 34px; height: 34px; border-radius: 50%; }
  .bank-card .bank-name { position: absolute; left: 103px; top: 20px; font-size: 19px; font-weight: 600; }
  .bank-card .acct { position: absolute; left: 103px; top: 46px; font-size: 17px; font-weight: 500; color: var(--muted); }
  .bank-card .more {
    position: absolute; right: 14px; top: 21px; width: 45px; height: 45px; border-radius: 50%;
    background: var(--dots); display: flex; align-items: center; justify-content: center; gap: 4px;
  }
  .more i { width: 5px; height: 5px; border-radius: 50%; background: #555; display: block; }
</style>
</head>
<body>
<div class="stage">

  <!-- Personal details -->
  <section class="phone phone--personal">
    <div class="status-bar">
      <svg class="back" width="14" height="22" viewBox="0 0 14 22"><path d="M11 3 3 11l8 8" fill="none" stroke="#fff" stroke-width="3.5" stroke-linecap="round" stroke-linejoin="round"/></svg>
      <svg class="indicators" width="82" height="20" viewBox="0 0 82 20"><g fill="#fff"><rect x="0" y="11" width="3" height="5"/><rect x="5" y="8" width="3" height="8"/><rect x="10" y="5" width="3" height="11"/><rect x="15" y="2" width="3" height="14"/></g><path d="M27 7a13 13 0 0 1 18 0M30 10.5a8 8 0 0 1 12 0" fill="none" stroke="#fff" stroke-width="2.5" stroke-linecap="round"/><circle cx="36" cy="14.5" r="2.3" fill="#fff"/><rect x="53" y="3" width="26" height="13" rx="2.5" fill="none" stroke="#fff" stroke-width="2"/><rect x="56" y="6" width="20" height="7" fill="#fff"/><rect x="80" y="7" width="2" height="5" fill="#fff"/></svg>
    </div>
    <div class="brand" style="top:135px"><span class="mark"></span><span class="name">Lendoro</span></div>
    <h1 class="screen-title" style="top:249px">Personal Details</h1>
    <div class="field" style="top:310px">Given Name :</div>
    <div class="field" style="top:375px">Middle Name :</div>
    <div class="field" style="top:440px">Surname :</div>
    <div class="field" style="top:505px">Date of Birth :</div>
    <div class="btn-next">NEXT</div>
    <nav class="nav-bar">
      <svg width="32" height="30" viewBox="0 0 32 30"><path d="M4 13 16 3l12 10v14H20v-9h-8v9H4z" fill="none" stroke="#fff" stroke-width="3" stroke-linejoin="round"/></svg>
      <svg width="30" height="30" viewBox="0 0 30 30"><circle cx="13" cy="13" r="10" fill="none" stroke="#fff" stroke-width="3"/><path d="m21 21 6 6" stroke="#fff" stroke-width="3" stroke-linecap="round"/></svg>
      <svg width="30" height="30" viewBox="0 0 30 30"><circle cx="15" cy="9" r="6" fill="none" stroke="#fff" stroke-width="3"/><path d="M3 27v-2a7 7 0 0 1 7-7h10a7 7 0 0 1 7 7v2z" fill="none" stroke="#fff" stroke-width="3" stroke-linejoin="round"/></svg>
    </nav>
  </section>

  <!-- Loan details -->
  <section class="phone phone--loan">
    <div class="status-bar">
      <svg class="back" width="14" height="22" viewBox="0 0 14 22"><path d="M11 3 3 11l8 8" fill="none" stroke="#fff" stroke-width="3.5" stroke-linecap="round" stroke-linejoin="round"/></svg>
      <svg class="indicators" width="82" height="20" viewBox="0 0 82 20"><g fill="#fff"><rect x="0" y="11" width="3" height="5"/><rect x="5" y="8" width="3" height="8"/><rect x="10" y="5" width="3" height="11"/><rect x="15" y="2" width="3" height="14"/></g><path d="M27 7a13 13 0 0 1 18 0M30 10.5a8 8 0 0 1 12 0" fill="none" stroke="#fff" stroke-width="2.5" stroke-linecap="round"/><circle cx="36" cy="14.5" r="2.3" fill="#fff"/><rect x="53" y="3" width="26" height="13" rx="2.5" fill="none" stroke="#fff" stroke-width="2"/><rect x="56" y="6" width="20" height="7" fill="#fff"/><rect x="80" y="7" width="2" height="5" fill="#fff"/></svg>
    </div>
    <div class="brand" style="top:121px"><span class="mark"></span><span class="name">Lendoro</span></div>
    <h1 class="screen-title" style="top:221px">Loan Details</h1>
    <p class="centered next-label">Next Repayment</p>
    <p class="centered amount">$XX</p>
    <p class="centered due">on 4 Dec</p>
    <div class="toggle"><span class="active">XXX</span><span>XXX</span></div>
    <div class="activities">
      <h2>Activities</h2>
      <div class="activity"><p class="label">Repayment</p><p class="date">DD MM YY</p><span class="value">$xx</span></div>
      <div class="activity"><p class="label">Repayment</p><p class="date">DD MM YY</p><span class="value">$xx</span></div>
    </div>
    <nav class="nav-bar">
      <svg width="32" height="30" viewBox="0 0 32 30"><path d="M4 13 16 3l12 10v14H20v-9h-8v9H4z" fill="none" stroke="#fff" stroke-width="3" stroke-linejoin="round"/></svg>
      <svg width="30" height="30" viewBox="0 0 30 30"><circle cx="13" cy="13" r="10" fill="none" stroke="#fff" stroke-width="3"/><path d="m21 21 6 6" stroke="#fff" stroke-width="3" stroke-linecap="round"/></svg>
      <svg width="30" height="30" viewBox="0 0 30 30"><circle cx="15" cy="9" r="6" fill="none" stroke="#fff" stroke-width="3"/><path d="M3 27v-2a7 7 0 0 1 7-7h10a7 7 0 0 1 7 7v2z" fill="none" stroke="#fff" stroke-width="3" stroke-linejoin="round"/></svg>
    </nav>
  </section>

  <!-- Bank details -->
  <section class="phone phone--bank">
    <div class="status-bar">
      <svg class="back" width="14" height="22" viewBox="0 0 14 22"><path d="M11 3 3 11l8 8" fill="none" stroke="#fff" stroke-width="3.5" stroke-linecap="round" stroke-linejoin="round"/></svg>
      <svg class="indicators" width="82" height="20" viewBox="0 0 82 20"><g fill="#fff"><rect x="0" y="11" width="3" height="5"/><rect x="5" y="8" width="3" height="8"/><rect x="10" y="5" width="3" height="11"/><rect x="15" y="2" width="3" height="14"/></g><path d="M27 7a13 13 0 0 1 18 0M30 10.5a8 8 0 0 1 12 0" fill="none" stroke="#fff" stroke-width="2.5" stroke-linecap="round"/><circle cx="36" cy="14.5" r="2.3" fill="#fff"/><rect x="53" y="3" width="26" height="13" rx="2.5" fill="none" stroke="#fff" stroke-width="2"/><rect x="56" y="6" width="20" height="7" fill="#fff"/><rect x="80" y="7" width="2" height="5" fill="#fff"/></svg>
    </div>
    <div class="brand" style="top:121px"><span class="mark"></span><span class="name">Lendoro</span></div>
    <h1 class="screen-title" style="top:221px">Bank Details</h1>
    <div class="bank-card" style="top:290px">
      <div class="tile"><span class="dot" style="background:#e31b23"></span></div>
      <p class="bank-name">Harbor Bank</p><p class="acct">1234567854546</p>
      <div class="more"><i></i><i></i><i></i></div>
    </div>
    <div class="bank-card" style="top:386px">
      <div class="tile"><span class="dot" style="background:#1466e0"></span></div>
      <p class="bank-name">Northgate</p><p class="acct">1234567854546</p>
      <div class="more"><i></i><i></i><i></i></div>
    </div>
    <div class="bank-card" style="top:483px">
      <div class="tile"><span class="dot" style="background:#ffcc00"></span></div>
      <p class="bank-name">Meridian Bank</p><p class="acct">1234567854546</p>
      <div class="more"><i></i><i></i><i></i></div>
    </div>
    <nav class="nav-bar">
      <svg width="32" height="30" viewBox="0 0 32 30"><path d="M4 13 16 3l12 10v14H20v-9h-8v9H4z" fill="none" stroke="#fff" stroke-width="3" stroke-linejoin="round"/></svg>
      <svg width="30" height="30" viewBox="0 0 30 30"><circle cx="13" cy="13" r="10" fill="none" stroke="#fff" stroke-width="3"/><path d="m21 21 6 6" stroke="#fff" stroke-width="3" stroke-linecap="round"/></svg>
      <svg width="30" height="30" viewBox="0 0 30 30"><circle cx="15" cy="9" r="6" fill="none" stroke="#fff" stroke-width="3"/><path d="M3 27v-2a7 7 0 0 1 7-7h10a7 7 0 0 1 7 7v2z" fill="none" stroke="#fff" stroke-width="3" stroke-linejoin="round"/></svg>
    </nav>
  </section>

</div>
</body>
</html>
```